A Label for an ECO Friendly Spirit Company

Design a label which can be used for vodka and gin (London Dry Gin). It should be Square type Like the Shape File you see in the uploads. KIRO means Kind Inventive Rare and Original. We want a cool and slim label that calls for eco-friendly. We want to use it for our premium
Vodka and our London Dry Gin. Please use the logo and design it in Square Type.

40%vol, 700ml

Target Market(s)

spirits and events

Industry/Entity Type

SPIRITS

Colors
00AB8E
00BBA5
67D7C9
C6EFE9
E9F9F6
59FF00
82FF00
B8FF75
E3FFCB
F4FFEA

Requirements
Must have
• Logo from KIRO, Squaee Shape

```html
<!DOCTYPE html>
<html lang="en">
<head>
<meta charset="utf-8">
<title>KIRO Premium Vodka Label</title>
<link rel="stylesheet" href="https://fonts.googleapis.com/css2?family=Montserrat:wght@300;500;700;800&display=swap">
<style>
  :root {
    --paper: #ffffff;
    --ink: #000000;
    --lime: #94c52e;
    --teal: #0aa98c;
    --white: #ffffff;
  }
  html, body {
    margin: 0;
    padding: 0;
    width: 1085px;
    height: 1200px;
    overflow: hidden;
    background: var(--paper);
  }
  .label {
    display: block;
    width: 1085px;
    height: 1200px;
    font-family: "Montserrat", sans-serif;
  }
  .label__cap { fill: var(--lime); }
  .label__field { fill: var(--ink); }
  .label__panel { fill: var(--teal); }
  .brand__mark { fill: var(--lime); }
  .brand__name {
    fill: var(--teal);
    font-weight: 500;
    font-size: 166px;
    letter-spacing: 2px;
  }
  .product__line { font-size: 48px; fill: var(--ink); letter-spacing: 1px; }
  .product__premium { font-weight: 300; }
  .product__spirit { font-weight: 800; }
  .spec__abv { fill: var(--white); font-weight: 700; font-size: 126px; }
  .spec__percent { fill: var(--white); font-weight: 700; font-size: 70px; }
  .spec__vol { fill: var(--white); font-weight: 500; font-size: 36px; }
  .spec__volume { fill: var(--white); font-weight: 700; font-size: 72px; }
</style>
</head>
<body>
<svg class="label" viewBox="0 0 1085 1200" xmlns="http://www.w3.org/2000/svg" role="img" aria-label="KIRO Premium Vodka square label, 40% vol, 700 ml">
  <defs>
    <clipPath id="diamond">
      <path d="M542,100 L1042,600 L542,1100 L42,600 Z"/>
    </clipPath>
    <path id="product-arc" d="M322,806 Q540,676 806,734"/>
  </defs>

  <g clip-path="url(#diamond)">
    <rect class="label__field" x="0" y="0" width="1085" height="1200"/>
    <path class="label__cap" d="M0,0 L1085,0 L1085,223 L664,223 Q520,224 446,197 L0,197 Z"/>
    <path class="label__panel" d="M275,754 Q540,615 827,677 Q800,830 707,938 L542,1100 L372,930 Q310,860 275,754 Z"/>
  </g>

  <g class="brand">
    <rect class="brand__mark" x="432" y="272" width="229" height="239" rx="18"/>
    <text class="brand__name" x="546" y="643" text-anchor="middle">KIRO</text>
  </g>

  <text class="product__line">
    <textPath href="#product-arc" startOffset="50%" text-anchor="middle"><tspan class="product__premium">PREMIUM </tspan><tspan class="product__spirit">VODKA</tspan></textPath>
  </text>

  <g class="spec">
    <text class="spec__abv" x="586" y="874" text-anchor="end">40</text>
    <text class="spec__percent" x="594" y="836">%</text>
    <text class="spec__vol" x="596" y="874">VOL</text>
    <text class="spec__volume" x="551" y="946" text-anchor="middle">700ML</text>
  </g>
</svg>
</body>
</html>
```